Pool Screen Enclosure Building a Career Boot Camp!

Looking to Host a Boot Camp for people looking for a career or looking to change careers. We Design, Manufacture and Install Custom Pool Screen Enclosures. We have a training program to allow Non Experienced motivated people the chance at a great career that will provide a great living for them and their family. This will be a paid boot camp, week long, we provide all the initial training for them to make a transition into our business. This will be 5 days of training with a guaranteed job to start the following Monday.... This is good for both someone with no construction experience or someone with construction experience that wants to upgrade their current job.
Paid Boot Camp
transition to a full time job with great pay
Benefits include Health Insurance, Dental and Vision, 401K, we provide the tools and training.

```html
<!DOCTYPE html>
<html lang="en">
<head>
<meta charset="utf-8">
<title>Screen Haven Co – Paid Boot Camp Flyer</title>
<link href="https://fonts.googleapis.com/css2?family=Oswald:wght@500;700&family=Open+Sans:wght@300;400;600&display=swap" rel="stylesheet">
<style>
  :root {
    --black: #050505;
    --yellow: #fcca3b;
    --green: #4cdc1f;
    --brand-green: #3fbf2a;
    --white: #ffffff;
    --ink: #333333;
    --backdrop: #e7e5e1;
  }
  * { margin: 0; padding: 0; box-sizing: border-box; }
  html, body { width: 707px; height: 1200px; overflow: hidden; background: var(--backdrop); }
  .flyer {
    position: absolute; left: 0; top: 142px; width: 707px; height: 916px;
    background: var(--white); overflow: hidden;
    font-family: "Open Sans", Arial, sans-serif; color: var(--ink);
  }
  .abs { position: absolute; }

  /* Header */
  .header-shape { left: 0; top: 0; width: 707px; height: 127px; }
  .brand { left: 50px; top: 39px; display: flex; align-items: center; gap: 12px; }
  .brand-dot { width: 40px; height: 40px; border-radius: 50%; background: var(--brand-green); }
  .brand-name { font-family: "Open Sans", Arial, sans-serif; font-weight: 600; font-size: 26px; color: var(--brand-green); line-height: 1.1; }
  .cta-kicker { left: 413px; top: 19px; font-family: "Oswald", sans-serif; font-weight: 500; font-style: oblique; font-size: 12px; color: var(--black); letter-spacing: .2px; }
  .cta-title { left: 413px; top: 35px; font-family: "Oswald", sans-serif; font-weight: 700; font-style: oblique; font-size: 18.5px; color: var(--black); letter-spacing: .2px; }
  .phone-bar { left: 400px; top: 67px; width: 290px; height: 40px; }
  .phone-number { left: 452px; top: 65px; font-family: "Oswald", sans-serif; font-weight: 700; font-style: oblique; font-size: 33px; color: var(--white); line-height: 42px; letter-spacing: 1px; }

  /* Photo collage */
  .collage { left: 0; top: 127px; width: 707px; height: 343px; }

  /* Headline band */
  .headline-band { left: 0; top: 470px; width: 707px; height: 91px; background: var(--green); text-align: center; padding-top: 7px; }
  .headline-band h1 { font-family: "Oswald", sans-serif; font-weight: 700; font-size: 30px; line-height: 39px; color: var(--white); text-transform: uppercase; letter-spacing: .3px; text-shadow: 0 1px 2px rgba(0,0,0,.25); }

  /* Intro */
  .intro { left: 0; top: 578px; width: 707px; text-align: center; font-weight: 300; font-size: 20px; line-height: 29px; color: #444; }
  .points { top: 648px; list-style: none; }
  .points.left { left: 51px; width: 290px; }
  .points.right { left: 376px; width: 300px; }
  .points li { position: relative; padding-left: 22px; font-size: 11px; line-height: 14.5px; color: #3a3a3a; margin-bottom: 21px; }
  .points.right li { margin-bottom: 14px; }
  .points li svg { position: absolute; left: 0; top: 1px; width: 13px; height: 13px; }

  /* Footer */
  .footer-rule { left: 0; top: 781px; width: 707px; height: 7px; background: var(--yellow); }
  .footer { left: 0; top: 788px; width: 707px; height: 128px; background: var(--black); }
  .bootcamp-title { left: 51px; top: 15px; font-family: "Oswald", sans-serif; font-weight: 700; font-size: 38px; line-height: 44px; color: var(--green); letter-spacing: .5px; }
  .perks { left: 51px; top: 63px; list-style: none; }
  .perks li { position: relative; padding-left: 18px; font-size: 11px; line-height: 18px; color: var(--white); }
  .perks li::before { content: ""; position: absolute; left: 1px; top: 6px; width: 6px; height: 6px; border-radius: 50%; background: var(--yellow); }
  .footer-divider { left: 405px; top: 24px; width: 1px; height: 88px; background: #777; }
  .contact-name { left: 448px; top: 21px; font-weight: 600; font-size: 17px; color: var(--brand-green); }
  .contacts { left: 448px; top: 53px; list-style: none; }
  .contacts li { display: flex; align-items: center; gap: 6px; font-size: 10.5px; line-height: 20px; color: var(--white); }
  .contacts svg { width: 14px; height: 14px; flex: none; }
  .contacts .hl { color: var(--brand-green); font-weight: 600; }
</style>
</head>
<body>
<main class="flyer">

  <!-- Header -->
  <svg class="abs header-shape" viewBox="0 0 707 127" aria-hidden="true">
    <rect width="707" height="127" fill="var(--yellow)"/>
    <polygon points="0,0 400,0 335,119 0,119" fill="var(--black)"/>
  </svg>
  <div class="abs brand">
    <span class="brand-dot"></span>
    <span class="brand-name">Screen Haven Co</span>
  </div>
  <p class="abs cta-kicker">ENCLOSE IT, SO YOU CAN USE IT</p>
  <p class="abs cta-title">GET A FREE DESIGN CONSULTATION</p>
  <svg class="abs phone-bar" viewBox="0 0 290 40" aria-hidden="true">
    <polygon points="8,0 60,0 52,40 0,40" fill="var(--green)"/>
    <polygon points="46,0 290,0 280,40 38,40" fill="var(--black)"/>
    <path d="M17 11c2-2 4-1 5 1l2 3c1 1 0 3-1 3l-1 1c1 3 3 5 6 6l1-1c1-1 2-1 3 0l3 2c1 1 1 3 0 4l-2 2c-6 1-17-10-16-16z" fill="var(--black)"/>
  </svg>
  <p class="abs phone-number">555-014-2286</p>

  <!-- Photo collage -->
  <svg class="abs collage" viewBox="0 0 922 447" preserveAspectRatio="none">
    <defs>
      <linearGradient id="g-pool" x1="0" y1="0" x2="0" y2="1">
        <stop offset="0" stop-color="#c9ced3"/><stop offset=".55" stop-color="#8f9a9c"/><stop offset=".8" stop-color="#5f8c8f"/><stop offset="1" stop-color="#c9a58c"/>
      </linearGradient>
      <linearGradient id="g-sky" x1="0" y1="0" x2="0" y2="1">
        <stop offset="0" stop-color="#5c93d6"/><stop offset=".6" stop-color="#c6d4e2"/><stop offset="1" stop-color="#b7a996"/>
      </linearGradient>
      <linearGradient id="g-frame" x1="0" y1="0" x2="0" y2="1">
        <stop offset="0" stop-color="#3b3e42"/><stop offset=".5" stop-color="#c8ccd0"/><stop offset="1" stop-color="#8d8a7f"/>
      </linearGradient>
      <linearGradient id="g-spa" x1="0" y1="0" x2="0" y2="1">
        <stop offset="0" stop-color="#9fc2e4"/><stop offset=".45" stop-color="#d7dde3"/><stop offset="1" stop-color="#2c6fc4"/>
      </linearGradient>
      <linearGradient id="g-plans" x1="0" y1="0" x2="1" y2="1">
        <stop offset="0" stop-color="#8a6a52"/><stop offset="1" stop-color="#d9d4cb"/>
      </linearGradient>
    </defs>
    <polygon role="img" aria-label="Finished screened pool enclosure overlooking a lake" points="0,0 548,0 437,447 0,447" fill="url(#g-pool)"/>
    <polygon role="img" aria-label="Installers fitting an enclosure roof frame under blue sky" points="560,0 740,0 725,270 500,270" fill="url(#g-sky)"/>
    <polygon role="img" aria-label="Worker on a ladder assembling enclosure framing" points="755,0 922,0 922,270 738,270" fill="url(#g-frame)"/>
    <polygon role="img" aria-label="Screened spa beside the water" points="493,282 705,282 682,447 452,447" fill="url(#g-spa)"/>
    <polygon role="img" aria-label="Team reviewing enclosure drawings" points="720,282 922,282 922,447 697,447" fill="url(#g-plans)"/>
  </svg>

  <!-- Headline -->
  <section class="abs headline-band">
    <h1>Pool Screen Enclosure<br>Building a Career Boot Camp</h1>
  </section>

  <!-- Intro -->
  <p class="abs intro">We Design, Manufacture<br>and Install Custom Pool Screen Enclosures.</p>

  <ul class="abs points left">
    <li><svg viewBox="0 0 14 14"><circle cx="7" cy="7" r="6" fill="none" stroke="var(--green)" stroke-width="1.2"/><path d="M4 7.2l2 2 4-4" fill="none" stroke="var(--green)" stroke-width="1.3"/></svg>We have a training program to allow Non Experienced motivated people the chance at a great career that will provide a great living for them and their family.</li>
    <li><svg viewBox="0 0 14 14"><circle cx="7" cy="7" r="6" fill="none" stroke="var(--green)" stroke-width="1.2"/><path d="M4 7.2l2 2 4-4" fill="none" stroke="var(--green)" stroke-width="1.3"/></svg>This will be a paid boot camp, week long, we provide all the initial training for them to make a transition into our business.</li>
  </ul>
  <ul class="abs points right">
    <li><svg viewBox="0 0 14 14"><circle cx="7" cy="7" r="6" fill="none" stroke="var(--green)" stroke-width="1.2"/><path d="M4 7.2l2 2 4-4" fill="none" stroke="var(--green)" stroke-width="1.3"/></svg>This will be 5 days of training with a guaranteed job to start the following Monday....</li>
    <li><svg viewBox="0 0 14 14"><circle cx="7" cy="7" r="6" fill="none" stroke="var(--green)" stroke-width="1.2"/><path d="M4 7.2l2 2 4-4" fill="none" stroke="var(--green)" stroke-width="1.3"/></svg>This is good for both someone with no construction experience or someone with construction experience that wants to upgrade their current job.</li>
  </ul>

  <!-- Footer -->
  <div class="abs footer-rule"></div>
  <footer class="abs footer">
    <h2 class="abs bootcamp-title">PAID BOOT CAMP</h2>
    <ul class="abs perks">
      <li>Transition to a full time job with great pay.</li>
      <li>Benefits include Health Insurance, Dental and Vision, 401K.</li>
      <li>We provide the tools and training.</li>
    </ul>
    <div class="abs footer-divider"></div>
    <p class="abs contact-name">Screen Haven Co</p>
    <ul class="abs contacts">
      <li><svg viewBox="0 0 14 14"><circle cx="7" cy="7" r="6.3" fill="none" stroke="var(--green)" stroke-width="1"/><path d="M7 3.3a2.4 2.4 0 0 1 2.4 2.4C9.4 7.5 7 10.5 7 10.5S4.6 7.5 4.6 5.7A2.4 2.4 0 0 1 7 3.3z" fill="var(--green)"/><circle cx="7" cy="5.7" r=".9" fill="var(--black)"/></svg>118 Harbor Palm Lane, Coral Bend FL 30412</li>
      <li><svg viewBox="0 0 14 14"><circle cx="7" cy="7" r="6.3" fill="none" stroke="var(--green)" stroke-width="1"/><rect x="3.8" y="4.8" width="6.4" height="4.4" fill="none" stroke="var(--green)" stroke-width=".9"/><path d="M3.8 4.8L7 7.4l3.2-2.6" fill="none" stroke="var(--green)" stroke-width=".9"/></svg><span>office@<span class="hl">screenhavenco</span>.com</span></li>
      <li><svg viewBox="0 0 14 14"><circle cx="7" cy="7" r="6.3" fill="none" stroke="var(--green)" stroke-width="1"/><circle cx="7" cy="7" r="3.5" fill="none" stroke="var(--green)" stroke-width=".9"/><path d="M3.5 7h7M7 3.5c-1.6 2-1.6 5 0 7M7 3.5c1.6 2 1.6 5 0 7" fill="none" stroke="var(--green)" stroke-width=".8"/></svg><span>www.<span class="hl">screenhavenco</span>.com</span></li>
    </ul>
  </footer>

</main>
</body>
</html>
```